Golf Brochure + Business Card Design Project – Kestrel Fitness.

Task Description

We are looking for a premium tri-fold brochure (8.5x11 letter, folded) plus a new business card design for Kestrel Fitness. Both need to look polished, elegant, and professional — something that would feel at home in a golf club environment.

Brochure Scope:
• Tri-fold brochure promoting our new golf-specific services
• Incorporate brand colors: deep hunter green, cream, and gold accents
• Clean, modern typography (professional, not playful)
• Layout will follow the copy provided (final copy attached, no rewriting needed)
• Imagery: mature golfers (50+), golf lifestyle shots, no generic stocky images
• Include QR code placement linking to booking page
• Deliverables: print-ready PDF with bleed/crop (CMYK), high-res PDF (digital), and source file (InDesign or Illustrator)

Business Card Scope:
• Front + back design
• Consistent with brand colors and fonts
• Space for name, title, phone, email, and website
• Deliverables: print-ready PDF with bleed/crop (CMYK) + source file (AI or InDesign)
• If possible, provide editable template for future staff cards

Timeline:
• First draft within 5–7 days
• 2 rounds of revisions included

Budget:
$300 USD (total for both brochure + business card)

I’ll provide finalized copy if you accept the project.
Project description (paste this whole block in that box)

We need a premium tri-fold brochure (8.5”×11” letter, folded) and a new business card design for Kestrel Fitness. This will be presented to golf course managers and members, so the look must be elegant, restrained, and country-club-classy.

Scope — Brochure
• Format: Tri-fold, 8.5”×11”. Please set 0.125” bleed on all sides and keep critical text ≥0.125–0.25” inside the trim.
• Purpose: Promote Kestrel Fitness’ golf-specific services for adults 50+.
• Copy: We will provide finalized copy in a Word doc after acceptance. No rewriting needed — please focus on layout and polish.
• Imagery (required):
• Golf-first images (ball on tee/green, mature golfers mid-swing, and golf course landscapes at golden hour).
• 1–2 real Kestrel Fitness gym photos on inside panels (trainer with client doing golf-relevant movement: stretch, rotation, balance).
• Visual style: Premium, quiet, lots of white/negative space, balanced grids; no clutter.
• Brand colors (required): Hunter Green #0C2E1F, Gold #CBA135, Cream #F5F2EB. Convert for CMYK print while preserving the look.
• Typography: Clean, legible serif + sans pairing (e.g., modern serif for headlines, humanist/neo-grotesk sans for body). You may propose suitable professional fonts; avoid playful/novelty fonts.
• Elements to include:
• Our logo (we will upload).
• QR code placement to booking page (we will supply the URL / QR asset).
• Simple icon treatment for the three complimentary options (Strength & Mobility, Stretch Therapy, Vitrascan + Assessment).
• Deliverables:
• Print-ready PDF (CMYK, with bleed & crop marks, PDF/X-1a or PDF/X-4)
• High-res digital PDF (no bleed)
• Source file (InDesign or Illustrator) + packaged fonts/links or outlined type as appropriate.

Scope — Business Card
• Size: 3.5”×2” (US standard) with 0.125” bleed; keep text ≥0.125” from trim.
• Front/back design; consistent with brochure branding.
• Fields: Name, Title, Phone, Email, Website, Address; optional small QR on back.
• Deliverables: Print-ready PDF (CMYK, bleed & crops) + Source file (AI/INDD). Provide an editable template for staff names.

Process & Timing
• Initial concept for brochure + card within 5–7 days of acceptance.
• 2 rounds of revisions included.
• Please start with a clean layout concept using placeholder images/text blocks; we’ll drop in final copy/assets immediately after acceptance.

Stock & Licensing
• You may propose stock images that fit the brief (we’re fine approving Pixelgrove or equivalent). Please note any license fees separately if needed.

Usage Rights
• We require full usage rights to the final designs for print & digital.

Target Market(s)

Golfers 50+ in Victoria, BC: quality-oriented, health-conscious, want to play longer, stronger, and pain-free. Country-club aesthetic; expect polished, professional materials.

Industry/Entity Type

Health & Fitness — Golf Performance / Longevity Studio

Font styles to use
Serif
Sans Serif

Requirements
Must have
• • Golf-first imagery + 1–2 real Kestrel Fitness photos inside. • Brand colors: #0C2E1F (Hunter Green), #CBA135 (Gold), #F5F2EB (Cream). • Premium, restrained layout; ample negative space; no clutter. • Clean professional serif + sans type pairing; highly legible. • Space for logo and QR code (booking). • Correct print specs (bleed, crops, CMYK). • Deliverables: print-ready PDFs (brochure + card), digital PDF, source files.
Nice to have
• • Subtle texture or grain in backgrounds (very light) to add sophistication. • A second brochure cover variation (ball on tee vs. course landscape) at concept stage.
Should not have
• • Cheesy/posed “stocky” groups; overly young models; beer/alcohol imagery. • Over-saturated greens/blues; gimmicky gradients or clip art. • Generic fitness/bodybuilding shots unrelated to golf performance.

```html
<!DOCTYPE html>
<html lang="en">
<head>
<meta charset="utf-8">
<title>Kestrel Fitness – Business Card</title>
<link href="https://fonts.googleapis.com/css2?family=Red+Hat+Display:wght@400;500;700&display=swap" rel="stylesheet">
<style>
  :root {
    --backdrop: #121212;
    --hunter: #0c2e1f;
    --hunter-light: #0f3a26;
    --gold: #cba135;
    --paper: #ffffff;
    --ink: #0c2e1f;
    --ink-soft: #16231c;
  }
  * { margin: 0; padding: 0; box-sizing: border-box; }
  html, body {
    width: 1200px;
    height: 957px;
    overflow: hidden;
    background: var(--backdrop);
    font-family: "Red Hat Display", sans-serif;
  }
  .card {
    position: absolute;
    left: 324px;
    width: 553px;
    height: 315px;
  }
  .card-front {
    top: 137px;
    background: linear-gradient(150deg, var(--hunter) 0%, var(--hunter-light) 100%);
  }
  .card-back {
    top: 505px;
    background: var(--paper);
  }

  /* Front: brand lockup */
  .brand-front {
    position: absolute;
    left: 72px;
    top: 70px;
    width: 160px;
    text-align: center;
  }
  .brand-front .brand-circle {
    width: 84px;
    height: 84px;
    margin: 0 auto 16px;
    border: 2px solid var(--gold);
    border-radius: 50%;
  }
  .brand-front .brand-name {
    color: var(--gold);
    font-weight: 700;
    font-size: 19px;
    letter-spacing: 2px;
    text-transform: uppercase;
    line-height: 1.3;
  }

  /* Front: pillars */
  .pillars {
    position: absolute;
    left: 296px;
    top: 87px;
    width: 190px;
  }
  .pillar {
    position: relative;
    height: 33px;
    margin-bottom: 21px;
  }
  .pillar svg {
    position: absolute;
    inset: 0;
  }
  .pillar-label {
    position: absolute;
    left: 29px;
    top: 50%;
    transform: translateY(-50%);
    color: var(--gold);
    font-weight: 500;
    font-style: italic;
    font-size: 18px;
    letter-spacing: 3.4px;
  }

  /* Back */
  .holder-name {
    position: absolute;
    left: 39px;
    top: 46px;
    color: var(--ink);
    font-weight: 700;
    font-size: 32px;
    letter-spacing: 0.2px;
  }
  .holder-title {
    position: absolute;
    left: 40px;
    top: 87px;
    color: var(--ink-soft);
    font-weight: 400;
    font-size: 14px;
    letter-spacing: 1.6px;
  }
  .contact-list {
    position: absolute;
    left: 40px;
    top: 185px;
    list-style: none;
  }
  .contact-list li {
    display: flex;
    align-items: center;
    height: 22px;
    margin-bottom: 12px;
    color: var(--ink-soft);
    font-weight: 700;
    font-size: 15px;
    letter-spacing: 2.6px;
  }
  .contact-list svg {
    width: 13px;
    height: 13px;
    margin-right: 8px;
    flex: none;
  }
  .contact-list .phone { font-size: 17px; letter-spacing: 3px; }

  .brand-back {
    position: absolute;
    left: 404px;
    top: 185px;
    width: 114px;
    text-align: center;
  }
  .brand-back .brand-circle {
    width: 50px;
    height: 50px;
    margin: 0 auto 9px;
    border: 2px solid var(--ink);
    border-radius: 50%;
  }
  .brand-back .brand-name {
    color: var(--ink);
    font-weight: 700;
    font-size: 12px;
    letter-spacing: 1.6px;
    text-transform: uppercase;
    line-height: 1.3;
  }
</style>
</head>
<body>

<section class="card card-front" aria-label="Card front">
  <div class="brand-front">
    <div class="brand-circle"></div>
    <p class="brand-name">Kestrel<br>Fitness</p>
  </div>

  <div class="pillars">
    <div class="pillar">
      <svg viewBox="0 0 190 33" width="190" height="33" aria-hidden="true">
        <path d="M0 1 H173.5 A15.5 15.5 0 0 1 173.5 32 H0" fill="none" stroke="#cba135" stroke-width="1.4"/>
      </svg>
      <span class="pillar-label">STRENGTH</span>
    </div>
    <div class="pillar">
      <svg viewBox="0 0 190 33" width="190" height="33" aria-hidden="true">
        <path d="M0 1 H173.5 A15.5 15.5 0 0 1 173.5 32 H0" fill="none" stroke="#cba135" stroke-width="1.4"/>
      </svg>
      <span class="pillar-label">MOBILITY</span>
    </div>
    <div class="pillar">
      <svg viewBox="0 0 190 33" width="190" height="33" aria-hidden="true">
        <path d="M0 1 H173.5 A15.5 15.5 0 0 1 173.5 32 H0" fill="none" stroke="#cba135" stroke-width="1.4"/>
      </svg>
      <span class="pillar-label">LONGEVITY</span>
    </div>
  </div>
</section>

<section class="card card-back" aria-label="Card back">
  <h1 class="holder-name">Maren-Lise Holloway</h1>
  <p class="holder-title">Owner | Kestrel Fitness</p>

  <ul class="contact-list">
    <li class="phone">
      <svg viewBox="0 0 16 16" aria-hidden="true"><path d="M3.5 1.5 L6 4 L4.6 5.6 C5.4 7.6 8.4 10.6 10.4 11.4 L12 10 L14.5 12.5 L12.6 14.4 C8 14 2 8 1.6 3.4 Z" fill="none" stroke="#16231c" stroke-width="1.1" stroke-linejoin="round"/></svg>
      250-555-0147
    </li>
    <li>
      <svg viewBox="0 0 16 16" aria-hidden="true"><rect x="1.5" y="3.5" width="13" height="9" fill="none" stroke="#16231c" stroke-width="1.1"/><path d="M1.5 3.5 L8 9 L14.5 3.5 M1.5 12.5 L6 8 M14.5 12.5 L10 8" fill="none" stroke="#16231c" stroke-width="1.1"/></svg>
      maren-lise@kestrelfitness.biz
    </li>
    <li>
      <svg viewBox="0 0 16 16" aria-hidden="true"><circle cx="8" cy="8" r="6.5" fill="none" stroke="#16231c" stroke-width="1.1"/><ellipse cx="8" cy="8" rx="3" ry="6.5" fill="none" stroke="#16231c" stroke-width="1"/><path d="M1.5 8 H14.5 M2.5 4.8 H13.5 M2.5 11.2 H13.5" stroke="#16231c" stroke-width="1"/></svg>
      www.kestrelfitness.biz
    </li>
  </ul>

  <div class="brand-back">
    <div class="brand-circle"></div>
    <p class="brand-name">Kestrel<br>Fitness</p>
  </div>
</section>

</body>
</html>
```